Print materials for 3-star hotel

We are changing up our print materials (notepads, letterheads, key card jackets, small flyer for the room rates) We are a 3 star business hotel in the Philippines and have mainly used grey tones and clean, simple lines. See attached photos for logo and hotel interior photos.

Target Market(s)

Business

Contact Information for Business Card

Corvale Terrace Hotel
Lindwell Banca Avenue corner Tolenta St Cebu City 6000 Philippines
Tel: +63 32 481 7302
Mobile: +63 917 648 2095
www.corvaleterracehotel.example

Font styles to use
Serif
Sans Serif

Requirements
Must have
• Simple
• Readable font and font size
Nice to have
• Neutral colors, grey and taupes
Should not have
• No purples and bright blues

```html
<!DOCTYPE html>
<html lang="en">
<head>
<meta charset="utf-8">
<title>Corvale Terrace Hotel — Business Card</title>
<link rel="stylesheet" href="https://fonts.googleapis.com/css2?family=Cinzel:wght@400;500&family=Roboto:wght@400;500&display=swap">
<style>
  :root {
    --backdrop: #2e2e2f;
    --card: #1d1d1e;
    --taupe: #d6c6ab;
    --taupe-soft: #b9a98f;
  }
  * { margin: 0; padding: 0; box-sizing: border-box; }
  html, body {
    width: 1200px;
    height: 900px;
    overflow: hidden;
    background: var(--backdrop);
  }
  .canvas {
    position: relative;
    width: 1200px;
    height: 900px;
  }
  .card {
    position: absolute;
    left: 290px;
    width: 620px;
    height: 354px;
    background: var(--card);
    box-shadow: 0 10px 28px rgba(0, 0, 0, 0.45);
    color: var(--taupe);
  }
  .card--brand { top: 50px; }
  .card--contact { top: 476px; }

  /* Brand side */
  .brand-lockup {
    position: absolute;
    left: 0; right: 0; top: 110px;
    text-align: center;
    font-family: "Cinzel", serif;
  }
  .brand-mark {
    display: block;
    width: 46px; height: 46px;
    margin: 0 auto 18px;
    background: var(--taupe);
  }
  .brand-name {
    font-size: 27px;
    letter-spacing: 5px;
    line-height: 1;
  }
  .brand-sub {
    font-size: 15px;
    letter-spacing: 6px;
    margin-top: 6px;
  }

  /* Contact side */
  .person {
    position: absolute;
    left: 48px; top: 62px;
  }
  .person-name {
    font-family: "Cinzel", serif;
    font-size: 25px;
    letter-spacing: 1px;
    line-height: 1;
  }
  .person-title-row {
    display: flex;
    align-items: flex-end;
    gap: 6px;
    margin-top: 4px;
    width: 526px;
  }
  .person-title {
    font-family: "Roboto", sans-serif;
    font-weight: 500;
    font-size: 14px;
    white-space: nowrap;
  }
  .rule {
    flex: 1;
    height: 1px;
    margin-bottom: 4px;
    background: var(--taupe-soft);
  }
  .details {
    position: absolute;
    left: 48px; top: 196px;
    font-family: "Roboto", sans-serif;
    font-size: 15px;
    line-height: 20px;
    list-style: none;
  }
  .details li { display: flex; align-items: center; gap: 8px; }
  .details .address { display: block; padding-left: 20px; }
  .details .address + li { margin-top: 8px; }
  .details svg { width: 13px; height: 13px; fill: var(--taupe); flex: none; }
  .corner-name {
    position: absolute;
    right: 44px; bottom: 40px;
    font-family: "Cinzel", serif;
    font-size: 34px;
    letter-spacing: 3px;
    line-height: 1;
  }
</style>
</head>
<body>
<main class="canvas">

  <section class="card card--brand" aria-label="Card front">
    <div class="brand-lockup">
      <span class="brand-mark" aria-hidden="true"></span>
      <div class="brand-name">CORVALE TERRACE</div>
      <div class="brand-sub">HOTEL</div>
    </div>
  </section>

  <section class="card card--contact" aria-label="Card back">
    <div class="person">
      <div class="person-name">DANIEL ARCEO</div>
      <div class="person-title-row">
        <span class="person-title">CEO/Founder</span>
        <span class="rule"></span>
      </div>
    </div>

    <ul class="details">
      <li class="address">4120 Alder Crest Road</li>
      <li class="address">Marlow Heights, Oregon 52810</li>
      <li>
        <svg viewBox="0 0 24 24" aria-hidden="true"><path d="M6.6 10.8a15.1 15.1 0 0 0 6.6 6.6l2.2-2.2a1 1 0 0 1 1-.25 11.4 11.4 0 0 0 3.6.57 1 1 0 0 1 1 1V20a1 1 0 0 1-1 1A17 17 0 0 1 3 4a1 1 0 0 1 1-1h3.5a1 1 0 0 1 1 1c0 1.25.2 2.45.57 3.57a1 1 0 0 1-.25 1z"/></svg>
        512 308 4417
      </li>
      <li>
        <svg viewBox="0 0 24 24" aria-hidden="true"><path d="M2 5h20v14H2z M2 5l10 8 10-8" fill="none" stroke="#d6c6ab" stroke-width="0"/><path d="M2 6.5 12 13l10-6.5V19H2z"/><path d="M2 5h20l-10 6.5z"/></svg>
        mail@cardhost.example
      </li>
      <li>
        <svg viewBox="0 0 24 24" aria-hidden="true"><circle cx="12" cy="12" r="10"/></svg>
        www.cardhost.example
      </li>
    </ul>

    <div class="corner-name">CORVALE</div>
  </section>

</main>
</body>
</html>
```